We need a business card design for a new company located in Brampton Ontario Canada. Our goal is to promote companies to use our service as an "External Program Management " firm taking their industrial product concepts " from prototype to production." We would like to use blue and yellow as our colors. Our skills include finding suppliers for prototype parts and developing them into supplying not only prototypes but the final production parts as well for our customer base.
Industry/Entity Type
Business
Contact Information for Business Card
Derek Namsby
Sales Manager
KOLVEN Solutions Inc.
14 Pinemarsh Lane
Brampton, Ontario L7P 2K9
Canada
Phone: 905-481-2976
Fax: 905-481-2976
website: www.kolvensolutions-example.com
Email: derek@kolvensolutions-example.com
Look and feel
Each slider illustrates characteristics of the customer's brand and the style your logo design should communicate.

```html
<!DOCTYPE html>
<html lang="en">
<head>
<meta charset="utf-8">
<title>KOLVEN Solutions Inc. — Business Card</title>
<link rel="stylesheet" href="https://fonts.googleapis.com/css2?family=Montserrat:wght@400;500;600&display=swap">
<style>
  :root {
    --backdrop: #3b3b3d;
    --card: #1d1d1f;
    --gold: #f6c419;
    --blue: #1f5fbf;
    --white: #f2f2f2;
    --muted: #cfcfcf;
  }
  * { margin: 0; padding: 0; box-sizing: border-box; }
  html, body { width: 1200px; height: 988px; overflow: hidden; }
  body {
    background: var(--backdrop);
    position: relative;
    font-family: "Montserrat", Arial, sans-serif;
  }
  .card {
    position: absolute;
    width: 560px;
    height: 320px;
    background: var(--card);
    border: 14px solid var(--gold);
    box-shadow: 0 18px 40px rgba(0,0,0,.45);
  }
  .card--back { left: 90px; top: 150px; }
  .card--front { left: 550px; top: 500px; }

  .corner-line { position: absolute; width: 100%; height: 100%; left: 0; top: 0; }

  .company {
    position: absolute; left: 0; right: 0;
    display: flex; align-items: center; justify-content: center; gap: 12px;
  }
  .company__mark { background: var(--blue); flex: none; }
  .company__name {
    font-family: "Montserrat", Arial, sans-serif;
    font-weight: 600;
    color: var(--gold);
    text-transform: uppercase;
    letter-spacing: 2px;
    white-space: nowrap;
    line-height: 1;
  }

  .card--front .company { top: 126px; }
  .card--front .company__mark { width: 24px; height: 24px; }
  .card--front .company__name { font-size: 28px; }

  .card--back .company { top: 44px; gap: 10px; }
  .card--back .company__mark { width: 18px; height: 18px; }
  .card--back .company__name { font-size: 21px; }

  .person {
    position: absolute; left: 0; right: 0; top: 100px;
    text-align: center; color: var(--white);
    text-transform: uppercase; letter-spacing: 2px;
  }
  .person__name { font-size: 15px; font-weight: 500; }
  .person__title { font-size: 10px; color: var(--muted); margin-top: 4px; }

  .contacts {
    position: absolute; left: 60px; right: 40px; top: 170px;
    display: grid; grid-template-columns: 1fr 1fr; row-gap: 10px; column-gap: 18px;
    color: var(--white); font-size: 10px;
  }
  .contact { display: flex; align-items: center; gap: 7px; white-space: nowrap; }
  .contact svg { width: 14px; height: 14px; flex: none; }
  .address {
    position: absolute; left: 60px; right: 40px; top: 226px;
    color: var(--white); font-size: 10px;
    display: flex; align-items: center; gap: 7px;
  }
  .address svg { width: 14px; height: 14px; }
</style>
</head>
<body>

<section class="card card--back" aria-label="Card back with contact details">
  <svg class="corner-line" viewBox="0 0 532 292" preserveAspectRatio="none">
    <polyline points="440,10 520,10 520,90" fill="none" stroke="#f2f2f2" stroke-width="1.5"/>
    <polyline points="12,200 12,282 92,282" fill="none" stroke="#f2f2f2" stroke-width="1.5"/>
  </svg>
  <div class="company">
    <span class="company__mark"></span>
    <span class="company__name">KOLVEN Solutions Inc.</span>
  </div>
  <div class="person">
    <p class="person__name">Derek Namsby</p>
    <p class="person__title">Sales Manager</p>
  </div>
  <div class="contacts">
    <p class="contact">
      <svg viewBox="0 0 16 16"><circle cx="8" cy="8" r="8" fill="#f2f2f2"/><path d="M5.2 4.2l1.4 1.6-.7 1a5 5 0 0 0 2.3 2.3l1-.7 1.6 1.4-.8 1.4C7.6 11 5 8.4 4.8 5z" fill="#1d1d1f"/></svg>
      905-481-2976
    </p>
    <p class="contact">
      <svg viewBox="0 0 16 16"><circle cx="8" cy="8" r="8" fill="#f2f2f2"/><path d="M5.2 4.2l1.4 1.6-.7 1a5 5 0 0 0 2.3 2.3l1-.7 1.6 1.4-.8 1.4C7.6 11 5 8.4 4.8 5z" fill="#1d1d1f"/></svg>
      905-481-2976
    </p>
    <p class="contact">
      <svg viewBox="0 0 16 16"><circle cx="8" cy="8" r="8" fill="#f2f2f2"/><rect x="4" y="5" width="8" height="6" fill="none" stroke="#1d1d1f" stroke-width="1.2"/><polyline points="4,5 8,8.5 12,5" fill="none" stroke="#1d1d1f" stroke-width="1.2"/></svg>
      derek@kolvensolutions-example.com
    </p>
    <p class="contact">
      <svg viewBox="0 0 16 16"><circle cx="8" cy="8" r="8" fill="#f2f2f2"/><circle cx="8" cy="8" r="4.5" fill="none" stroke="#1d1d1f" stroke-width="1"/><line x1="3.5" y1="8" x2="12.5" y2="8" stroke="#1d1d1f" stroke-width="1"/><ellipse cx="8" cy="8" rx="2" ry="4.5" fill="none" stroke="#1d1d1f" stroke-width="1"/></svg>
      www.kolvensolutions-example.com
    </p>
  </div>
  <p class="address">
    <svg viewBox="0 0 16 16"><circle cx="8" cy="8" r="8" fill="#f2f2f2"/><path d="M8 3.5a3 3 0 0 1 3 3c0 2.3-3 6-3 6s-3-3.7-3-6a3 3 0 0 1 3-3z" fill="#1d1d1f"/><circle cx="8" cy="6.5" r="1" fill="#f2f2f2"/></svg>
    14 Pinemarsh Lane, Brampton ON L7P 2K9
  </p>
</section>

<section class="card card--front" aria-label="Card front with company name">
  <svg class="corner-line" viewBox="0 0 532 292" preserveAspectRatio="none">
    <polyline points="420,12 516,12 516,120" fill="none" stroke="#f2f2f2" stroke-width="1.5"/>
    <polyline points="16,170 16,280 120,280" fill="none" stroke="#f2f2f2" stroke-width="1.5"/>
  </svg>
  <div class="company">
    <span class="company__mark"></span>
    <span class="company__name">KOLVEN Solutions Inc.</span>
  </div>
</section>

</body>
</html>
```